Creation of a Velmaro website

Velmaro is a company% 26 # 233; t% 26 # 233; consulting that accompanies Swiss companies or% 26 # 233; strang% 26 # 232; res in the d% 26 # 233; development of their business on the market% 26 # 233; Switzerland by providing strategic contacts (personalized contact program% 26 # 233; s) or market information% 26 # 233; (% 26 # 233; market research% 26 # 233;) and by providing administrative support (repr% 26 # 233; tax representation) or logistics (organization of% 26 # 233; v% 26 # 233; nement, assistance for participation% 26 # 224; fairs). Our customers are mainly European companies wishing to develop their business in Switzerland. N% 26 # 233; however, our services are% 26 # 233; also aimed at Swiss companies wishing to develop in other parts of Switzerland. Our site must therefore be% 26 # 234; capable of being translated into several languages. The services offered% 26 # 233; s by Velmaro may also% 26 # 233; also% 26 # 39;% 26 # 233; tender% 26 # 224; promoting tourism in Switzerland for countries or regions% 26 # 233; foreigners or% 26 # 224; the promotion of trade fairs or fairs with% 26 # 232; sd% 26 # 39; companies of the sectors concerned% 26 # 233; s. It is therefore n% 26 # 233; necessary to be able to add sub-headings of services which can% 26 # 234; be displayed% 26 # 233; es or hide% 26 # 233; es as required. We are 2 associates% 26 # 233; s, low% 26 # 233; s in the French-speaking parts (Neuch% 26 # 226; tel) and al% 26 # 233; manique (Zurich) of Switzerland.

Target Market(s)

Swiss or European companies wishing to develop their activities in Switzerland.

Coding

Coded - Design and coding required

Colors

Designer to choose colors to be used in the design.

Requirements
Must have
• A home page A section of% 26 # 233; writing the services offered% 26 # 233; es by Velmaro with the possibility% 26 # 233; d% 26 # 39; add sub-headings which can% 26 # 234; be displayed% 26 # 233; e or hidden% 26 # 233; e A page with the r% 26 # 233; f% 26 # 233; which can be displayed% 26 # 233; e or hidden% 26 # 233; e A page of% 26 # 233; writing l% 26 # 39;% 26 # 233; team A page with form contact, addresses and int card% 26 # 233; gr% 26 # 233; e The site must% 26 # 234; be low% 26 # 233; on a CMS allowing% 26 # 39;% 26 # 234; to be autonomous in modifying the website The possibility% 26 # 233; to be able to translate the site into several languages (FR, EN, DE, IT, NL, ...)

```html
<!DOCTYPE html>
<html lang="en">
<head>
<meta charset="utf-8">
<title>Velmaro – Business Development Consulting</title>
<link href="https://fonts.googleapis.com/css2?family=Lato:ital,wght@0,300;0,400;0,700;0,900;1,400&family=Montserrat:wght@300;400&display=swap" rel="stylesheet">
<style>
:root{
  --navy:#1f3d5a;
  --navy-deep:#17314a;
  --navy-soft:#2b4b68;
  --ink:#22384f;
  --text:#5a5f66;
  --line:#c9ced4;
  --white:#ffffff;
  --lilac:#e9e8fb;
  --photo-warm:#a88b6e;
  --photo-cool:#51606e;
}
*{box-sizing:border-box;margin:0;padding:0}
html,body{width:1200px;height:4060px;overflow:hidden}
body{position:relative;background:var(--white);font-family:'Lato',sans-serif;color:var(--text)}
.abs{position:absolute}
.brand-word{font-family:'Montserrat',sans-serif;font-weight:300;letter-spacing:3px;color:var(--ink)}
.brand-mark{background:var(--navy);border-radius:8px}
.social{display:flex;gap:12px}
.social span{width:32px;height:32px;border:2px solid var(--ink);border-radius:50%;display:block}

/* header */
.topbar-line{left:112px;top:59px;width:976px;height:1px;background:var(--line)}
.lang{left:1000px;top:16px;font-size:19px;color:var(--ink)}
.nav{left:596px;top:86px;display:flex;font-size:17px;color:var(--ink)}
.nav a{color:inherit;text-decoration:none;padding:0 19px;border-left:1px solid #999}
.nav a:first-child{border-left:none}
.nav a:last-child{padding-right:0}

/* hero */
.hero{left:0;top:140px;width:1200px;height:554px;background:linear-gradient(120deg,#cfc6b8 0%,var(--photo-warm) 35%,#6a5849 65%,var(--photo-cool) 100%)}
.hero-mark{left:115px;top:350px;width:88px;height:88px;background:var(--white);border-radius:14px}
.hero-word{left:248px;top:352px;font-size:76px;color:var(--white);font-family:'Montserrat',sans-serif;font-weight:300;letter-spacing:6px}
.dots{display:flex;gap:8px}
.dots i{width:12px;height:12px;border-radius:50%;background:var(--white);display:block}

.rule{height:4px;background:var(--navy)}
h2.title{font-size:40px;font-weight:400;color:var(--ink)}
h2.title b{font-weight:700}
.para{font-size:17px;line-height:36px;text-align:justify}
.btn{display:inline-block;background:var(--navy);color:var(--white);font-size:17px;text-align:center}

/* welcome */
.video{left:684px;top:853px;width:404px;height:257px;background:linear-gradient(135deg,#3c4d5c,#8b7a6a 55%,#c8c0b4);box-shadow:0 20px 40px rgba(120,110,230,.2)}
.play{left:855px;top:950px;width:62px;height:62px;border-radius:50%;background:var(--navy-deep)}

/* process */
.process-photo{left:0;top:1254px;width:550px;height:615px;background:linear-gradient(160deg,#e6e4e1,#b9b3ad 60%,#8e8c8b)}
.process-panel{left:550px;top:1353px;width:650px;height:516px;background:linear-gradient(135deg,var(--navy-soft),var(--navy) 60%,var(--navy-deep));color:var(--white)}

/* services */
.card{width:276px;height:292px;background:var(--white);border:2px solid #e6e8ee;border-bottom:8px solid var(--navy);box-shadow:0 4px 14px rgba(0,0,0,.08);overflow:hidden}
.card .blob{position:absolute;right:-20px;top:-50px;width:110px;height:110px;border-radius:50%;background:var(--lilac)}
.card .icon{position:absolute;left:18px;top:18px;width:82px;height:82px;border-radius:50%;background:var(--navy)}
.card h3{position:absolute;left:18px;top:122px;font-size:18px;font-weight:700;color:var(--ink)}
.card p{position:absolute;left:20px;top:156px;width:236px;font-size:13.5px;line-height:25px}
.card .more{position:absolute;left:22px;top:244px;font-size:14px;font-weight:700;color:var(--ink)}

/* testimonial */
.test-photo{left:0;top:2591px;width:1200px;height:416px;background:linear-gradient(90deg,#4e5a68,#8a7766 45%,#b39d86 70%,#5f6f66)}
.quote-box{left:530px;top:2722px;width:538px;height:369px;background:var(--navy)}
.qmark{font-family:Georgia,serif;font-size:110px;line-height:1;color:var(--white)}

/* clients */
.client{width:209px;height:106px;border:2px solid #e0e3e8;border-radius:6px;display:flex;align-items:center;justify-content:center;gap:8px;font-size:20px;font-weight:700;color:var(--ink)}
.client i{width:18px;height:18px;border-radius:50%;background:var(--ink);display:block}

/* footer */
.footer{left:0;top:3624px;width:1200px;height:436px;background:linear-gradient(135deg,#2f4f6c,var(--navy) 70%);color:var(--white)}
.footer h4{position:absolute;font-size:24px;font-weight:700}
.ficon{position:absolute;width:50px;height:50px;border-radius:50%;background:var(--white)}
.footer .social span{border-color:var(--white)}
</style>
</head>
<body>

<!-- header -->
<div class="abs social" style="left:112px;top:15px"><span aria-label="Social link"></span><span aria-label="Social link"></span><span aria-label="Social link"></span></div>
<div class="abs lang">English &#x2304;</div>
<div class="abs topbar-line"></div>
<div class="abs brand-mark" style="left:112px;top:78px;width:40px;height:40px"></div>
<div class="abs brand-word" style="left:174px;top:78px;font-size:34px">VELMARO</div>
<nav class="abs nav"><a>Home</a><a>About Us</a><a>Service</a><a>Careers</a><a>Contact Us</a></nav>

<!-- hero -->
<div class="abs hero" role="img" aria-label="Team of colleagues working together at laptops in a bright office"></div>
<div class="abs hero-mark"></div>
<div class="abs hero-word">VELMARO</div>
<div class="abs dots" style="left:572px;top:645px"><i></i><i></i><i style="background:var(--navy)"></i></div>

<!-- welcome -->
<div class="abs rule" style="left:113px;top:777px;width:149px"></div>
<h2 class="abs title" style="left:113px;top:800px"><b>Welcome To</b> Velmaro</h2>
<p class="abs para" style="left:113px;top:868px;width:527px">Lorem ipsum dolor sit amet, consectetur adipiscing elit, sed do eiusmod tempor incididunt ut labore et dolore magna aliqua. Quis ipsum suspendisse ultrices gravida. Risus commodo viverra maecenas accumsan lacus vel facilisis. consectetur adipiscing elit, sed do eiusmod tempor incididunt ut labore et dolore magna aliqua. Quis ipsum suspendisse ultrices gravida. Risus commodo viverra maecenas accumsan lacus vel facilisis.</p>
<a class="abs btn" style="left:113px;top:1150px;width:138px;line-height:42px">Read More</a>
<div class="abs video" role="img" aria-label="Video preview of colleagues reviewing documents together"></div>
<div class="abs play"></div>
<svg class="abs" style="left:876px;top:969px" width="24" height="26" viewBox="0 0 24 26"><path d="M2 1 L22 13 L2 25Z" fill="#fff"/></svg>

<!-- process -->
<div class="abs process-photo" role="img" aria-label="Two smiling professionals looking at a tablet"></div>
<div class="abs process-panel">
  <div class="abs" style="left:59px;top:67px;width:149px;height:4px;background:var(--white)"></div>
  <h2 class="abs" style="left:59px;top:86px;font-size:40px;font-weight:400"><b>Our</b> Process</h2>
  <p class="abs" style="left:59px;top:161px;font-size:30px;line-height:48px;width:500px">We are optimists who love to work together</p>
  <p class="abs para" style="left:59px;top:270px;width:470px;color:#e8edf2">Lorem ipsum dolor sit amet, consectetur adipiscing elit, sed do eiusmod tempor incididunt ut labore et dolore magna aliqua. Quis ipsum suspendisse ultrices gravida. Risus commodo</p>
  <a class="abs btn" style="left:59px;top:402px;width:138px;line-height:43px;background:var(--white);color:var(--ink)">Read More</a>
</div>

<!-- services -->
<div class="abs rule" style="left:110px;top:1971px;width:150px"></div>
<h2 class="abs title" style="left:110px;top:1985px"><b>Our</b> Services</h2>
<p class="abs para" style="left:113px;top:2052px;width:580px;text-align:left">Lorem ipsum dolor sit amet, consectetur adipiscing elit, sed do eiusmod tempor incididunt ut labore et dolore magna aliqua.</p>

<div class="abs card" style="left:110px;top:2178px"><div class="blob"></div><div class="icon" role="img" aria-label="Market research icon"></div><h3>Market Research</h3><p>Lorem ipsum dolor sit amet, consectetur adipiscing elit, sed do eiusmod tempor.</p><div class="more">Read More &raquo;</div></div>
<div class="abs card" style="left:434px;top:2178px"><div class="blob"></div><div class="icon" role="img" aria-label="Tax representation icon"></div><h3>Tax Representation</h3><p>Lorem ipsum dolor sit amet, consectetur adipiscing elit, sed do eiusmod tempor.</p><div class="more">Read More &raquo;</div></div>
<div class="abs card" style="left:762px;top:2178px"><div class="blob"></div><div class="icon" role="img" aria-label="Logistics icon"></div><h3>Logistics</h3><p>Lorem ipsum dolor sit amet, consectetur adipiscing elit, sed do eiusmod tempor.</p><div class="more">Read More &raquo;</div></div>

<!-- testimonial -->
<div class="abs test-photo" role="img" aria-label="Colleagues in a warm office setting"></div>
<div class="abs" style="left:110px;top:2720px;width:149px;height:4px;background:var(--white)"></div>
<div class="abs" style="left:110px;top:2745px;color:var(--white);font-size:30px;font-weight:300">What Our Happy</div>
<div class="abs" style="left:110px;top:2790px;color:var(--white);font-size:36px;font-weight:400">Clients Say</div>
<div class="abs qmark" style="left:510px;top:2750px">&ldquo;</div>
<div class="abs quote-box">
  <p class="abs" style="left:52px;top:52px;width:450px;font-size:17px;line-height:32px;font-weight:700;color:var(--white)">Lorem ipsum dolor sit amet, consectetur adipiscing elit, sed do eiusmod tempor incididunt ut labore et dolore magna aliqua. Quis ipsum suspendisse ultrices gravida. Risus commodo viverra maecenas accumsan lacus vel</p>
  <div class="abs" role="img" aria-label="Customer portrait" style="left:52px;top:210px;width:76px;height:76px;border-radius:50%;background:linear-gradient(#d8d2cc,#9a8d80);border:3px solid var(--white)"></div>
  <div class="abs" style="left:158px;top:236px;font-size:17px;font-weight:700;color:var(--white)">- DANIEL R.</div>
  <div class="abs" style="left:164px;top:264px;font-size:15px;font-style:italic;color:#dfe6ec">Customer</div>
  <div class="abs dots" style="left:224px;top:338px"><i></i><i></i><i></i></div>
</div>
<div class="abs qmark" style="left:1038px;top:3010px;color:var(--navy)">&rdquo;</div>

<!-- clients -->
<div class="abs rule" style="left:494px;top:3207px;width:123px"></div>
<h2 class="abs title" style="left:0;top:3220px;width:1200px;text-align:center"><b>Our</b> Clients</h2>
<div class="abs client" style="left:113px;top:3354px"><i></i>BRACKENLY</div>
<div class="abs client" style="left:369px;top:3354px"><i></i>Vantora</div>
<div class="abs client" style="left:626px;top:3354px"><i></i>ORVANE</div>
<div class="abs client" style="left:880px;top:3354px"><i></i>Halcyra</div>
<div class="abs dots" style="left:572px;top:3523px;align-items:center"><i style="width:18px;height:18px;border:3px solid var(--navy);background:var(--white)"></i><i style="background:var(--navy);width:10px;height:10px"></i><i style="background:var(--navy);width:10px;height:10px"></i></div>

<!-- footer -->
<footer class="abs footer">
  <div class="abs" style="left:113px;top:76px;width:30px;height:30px;background:var(--white);border-radius:6px"></div>
  <div class="abs brand-word" style="left:158px;top:74px;font-size:28px;color:var(--white)">VELMARO</div>
  <p class="abs" style="left:114px;top:136px;width:310px;font-size:15px;line-height:28px">Lorem ipsum dolor sit amet, consectetur adipiscing elit, sed do eiusmod tempor incididunt ut labore..</p>
  <div class="abs social" style="left:110px;top:249px"><span></span><span></span><span></span></div>

  <h4 style="left:483px;top:64px">Contact Us</h4>
  <div class="ficon" style="left:486px;top:140px"></div>
  <svg class="abs" style="left:502px;top:152px" width="18" height="26" viewBox="0 0 18 26"><path d="M9 1a8 8 0 0 0-8 8c0 6 8 16 8 16s8-10 8-16a8 8 0 0 0-8-8z" fill="#1f3d5a"/><circle cx="9" cy="9" r="3" fill="#fff"/></svg>
  <div class="abs" style="left:550px;top:140px;font-size:20px;line-height:32px">Linden Court 7,<br>2000 Neuchâtel</div>
  <div class="ficon" style="left:486px;top:208px"></div>
  <svg class="abs" style="left:500px;top:222px" width="22" height="22" viewBox="0 0 22 22"><path d="M5 1l4 5-2 3c1 3 4 6 6 6l3-2 5 4-3 4C9 21 1 13 1 4z" fill="#1f3d5a"/></svg>
  <div class="abs" style="left:563px;top:218px;font-size:20px">555-014-2290</div>
  <div class="ficon" style="left:486px;top:282px"></div>
  <svg class="abs" style="left:500px;top:299px" width="22" height="16" viewBox="0 0 22 16"><rect width="22" height="16" rx="2" fill="#1f3d5a"/><path d="M1 1l10 8 10-8" stroke="#fff" stroke-width="1.5" fill="none"/></svg>
  <div class="abs" style="left:563px;top:294px;font-size:18px">info@velmaro.com</div>

  <h4 style="left:800px;top:64px">Subscribe News Latter</h4>
  <div class="abs" style="left:801px;top:136px;width:287px;height:48px;background:var(--white);border:2px solid #cfd6de"></div>
  <div class="abs" style="left:820px;top:151px;font-size:14px;color:#333">Enter Your Email</div>
  <div class="abs" style="left:1024px;top:138px;width:62px;height:44px;background:var(--navy)"></div>
  <svg class="abs" style="left:1043px;top:149px" width="24" height="22" viewBox="0 0 24 22"><path d="M23 1L1 10l7 3 2 8 4-6 6 4z" fill="#fff"/></svg>

  <div class="abs" style="left:113px;top:382px;font-size:16px">Copyrights 2020 All rights reserved</div>
</footer>

</body>
</html>
```